Business Card Design for Training Business

Clear Path Coaching is a new business that delivers training and other services with a focus on topics related to mental health and wellbeing, for example, Wellmind Response Course, Resilience etc. We have a strong focus on evidence-based psychology and neuroscience. I have a logo which I will upload with the brief, so please consider colours that work well with the logo.
Target Market(s)
Adults, workplaces (particularly government and not-for-profits)
Industry/Entity Type
Business
Contact Information for Business Card
Head Strong TrainingSamantha SellwoodDirector0438 770 850sam@headstrongtraining.com.auwww.headstrongtraining.com.au

```html
<!DOCTYPE html>
<html lang="en">
<head>
<meta charset="utf-8">
<title>Clear Path Coaching – Business Card</title>
<link href="https://fonts.googleapis.com/css2?family=Questrial&display=swap" rel="stylesheet">
<style>
  :root {
    --teal: #22b8be;
    --teal-soft: #bfe9ea;
    --grey-band: #8a8a8a;
    --grey-text: #6f6f6f;
    --card: #f9f9f9;
    --page: #3a3a3a;
    --white: #ffffff;
  }
  * { box-sizing: border-box; margin: 0; padding: 0; }
  html, body { width: 1200px; height: 750px; overflow: hidden; }
  body {
    background: var(--page);
    font-family: "Questrial", "Century Gothic", sans-serif;
    position: relative;
  }
  .card {
    position: absolute;
    left: 312px;
    width: 576px;
    height: 330px;
    border-radius: 16px;
    background: var(--card);
    overflow: hidden;
  }
  .card--front { top: 33px; }
  .card--back { top: 387px; }

  .wave { position: absolute; inset: 0; width: 576px; height: 330px; }

  .brand {
    position: absolute;
    left: 12px;
    top: 32px;
    width: 240px;
    text-align: center;
    color: var(--grey-text);
  }
  .brand__dot {
    display: block;
    width: 82px; height: 82px;
    margin: 0 auto 14px;
    border-radius: 50%;
    background: var(--teal-soft);
  }
  .brand__name {
    font-size: 25px;
    letter-spacing: 2px;
    line-height: 1;
    white-space: nowrap;
  }
  .brand__sub {
    margin-top: 8px;
    font-size: 12px;
    letter-spacing: 5px;
    line-height: 1;
  }

  .person {
    position: absolute;
    right: 26px;
    top: 194px;
    text-align: right;
    color: var(--white);
  }
  .person__name { font-size: 23px; line-height: 1; }
  .person__role { font-size: 17px; line-height: 1; margin-top: 4px; }

  .contacts {
    position: absolute;
    right: 26px;
    top: 248px;
    list-style: none;
    color: var(--white);
    font-size: 15px;
  }
  .contacts li {
    display: flex;
    justify-content: flex-end;
    align-items: center;
    gap: 10px;
    height: 22px;
  }
  .contacts svg { width: 16px; height: 16px; flex: none; }

  .back__dot {
    position: absolute;
    left: 219px; top: 97px;
    width: 138px; height: 138px;
    border-radius: 50%;
    background: var(--teal-soft);
  }
  .back__url {
    position: absolute;
    left: 0; right: 0;
    top: 285px;
    text-align: center;
    font-size: 15px;
    color: #555;
  }
</style>
</head>
<body>

  <section class="card card--front">
    <svg class="wave" viewBox="0 0 576 330" aria-hidden="true">
      <path d="M0,205 C60,240 120,262 200,246 C300,222 380,50 500,44 C540,42 560,46 576,52 L576,330 L0,330 Z" fill="var(--grey-band)"/>
      <path d="M0,228 C60,262 120,285 200,266 C300,242 380,60 500,52 C540,50 560,54 576,60 L576,330 L0,330 Z" fill="var(--teal)" stroke="var(--white)" stroke-width="3"/>
    </svg>

    <div class="brand">
      <span class="brand__dot"></span>
      <div class="brand__name">CLEAR PATH</div>
      <div class="brand__sub">COACHING</div>
    </div>

    <div class="person">
      <div class="person__name">Rebecca Tanfield</div>
      <div class="person__role">Director</div>
    </div>

    <ul class="contacts">
      <li>0491 362 517
        <svg viewBox="0 0 16 16" aria-label="phone"><path fill="#fff" d="M3.5 1.5 6 1l1.3 3.3-1.6 1.2c.8 1.8 2.2 3.2 4 4l1.2-1.6L14.2 9l-.5 2.5c-.2.9-1 1.5-1.9 1.4C6.6 12.4 2.9 8.6 2.6 3.4c0-.9.5-1.7 1-1.9z"/></svg>
      </li>
      <li>bec@clearpathcoaching.example.au
        <svg viewBox="0 0 16 16" aria-label="email"><rect x="1" y="3.5" width="14" height="9" fill="#fff"/><path d="M1.5 4 8 9l6.5-5" fill="none" stroke="var(--teal)" stroke-width="1"/></svg>
      </li>
      <li>www.clearpathcoaching.example.au
        <svg viewBox="0 0 16 16" aria-label="website"><circle cx="8" cy="8" r="7" fill="#fff"/><path d="M5 4c1 1 2 1 2 2.5S5 8 5 9.5 7 11 7 13M10 3c-.5 1.5.5 2.5 2 2.5M11 9c-1 .5-1 2 0 3" fill="none" stroke="var(--teal)" stroke-width="1.3"/></svg>
      </li>
    </ul>
  </section>

  <section class="card card--back">
    <span class="back__dot"></span>
    <div class="back__url">www.clearpathcoaching.example.au</div>
  </section>

</body>
</html>
```